The Harbourlight Dental centre, the Zorvik of dentistry

New concept of running a dental practice by having a walk in practice
WE ARE A HUSBAND AND WIFE TEAM

Really modern and sophisticated, we want it to feel different from the traditional dental practice.
we want it split into different pages:CONTACT US
LOCATION: Information about our location since patients often confuse us with the practice across the road
ABOUT US:
Opening hours - & 7 Days, We offer a weekend service
WALK IN: We offer a walk in service for dental treatments
TREATMENTS we offer

DENTAL ADVICE: Free dentist advise call back- So a dentist will call you back for free to discuss

Target Market(s)

Everyone

Industry/Entity Type

Dental

Coding

Coded - Design and coding required

Number of Pages Required

5+ page

Requirements
Must have
• First page
• * changing pictures
• *opening times
• * our walk in concept I.e. no appointment needed
• *logo
• * links in to clinic tidal (online booking system in Australia)
• * address /phone number/email
• * possible videos
• Second page
• meet the team
• third page
• dental treatments/walk in treatments
• fourth page
• dental advice with vid larko videos
• Fifth page
• contact us/maps/ we get confused with the dental practice across the road
• We would also like a giving back page. In this please include the photo's below of our dental mission in Guatemala, where by we did treatment for patients as part of a charity.
Nice to have
• Changing pictures on the home screen
• videos linked to home page

```html
<!DOCTYPE html>
<html lang="en">
<head>
<meta charset="utf-8">
<title>The Harbourlight Dental Centre</title>
<link rel="stylesheet" href="https://fonts.googleapis.com/css2?family=Raleway:wght@400;500;600;700;800&display=swap">
<style>
:root{
  --blue:#1fa9e1;
  --blue-dark:#0e95cf;
  --green:#8cc63f;
  --green-dark:#6fa82a;
  --text:#5d6166;
  --heading:#3f4246;
  --light-bg:#f5f5f5;
  --footer:#4b4b4b;
  --footer-bottom:#3c3c3c;
  --white:#ffffff;
}
*{margin:0;padding:0;box-sizing:border-box}
html,body{width:1200px;height:2214px;overflow:hidden}
body{font-family:"Raleway",sans-serif;color:var(--text);background:var(--white);position:relative}
.abs{position:absolute}
a{color:inherit;text-decoration:none}

/* header */
.top-line{left:0;top:0;width:1200px;height:4px;background:linear-gradient(90deg,var(--green) 0 50%,var(--blue) 50% 100%)}
.brand{left:77px;top:30px;display:flex;align-items:center;gap:10px}
.brand-mark{width:34px;height:34px;border-radius:50%;background:var(--blue)}
.brand-name{font-size:21px;font-weight:700;color:var(--green);line-height:1}
.brand-sub{font-size:8px;letter-spacing:2px;font-weight:700;color:var(--green);margin-top:4px}
.info-block{top:24px;font-size:13px;font-weight:600;color:var(--heading);line-height:22px}
.info-block h4{font-size:11.5px;color:var(--green);font-weight:700;margin-bottom:6px}
.info-row{display:flex;align-items:center;gap:10px}
.info-row svg{width:13px;height:13px;fill:var(--heading)}

.nav{left:0;top:108px;width:1200px;height:46px;background:linear-gradient(180deg,#2bb8ee,var(--blue-dark))}
.nav a{position:absolute;top:0;line-height:46px;color:var(--white);font-size:12.5px;font-weight:700;letter-spacing:.3px}

/* hero */
.hero{left:0;top:154px;width:1200px;height:478px;overflow:hidden;
  background:
    radial-gradient(ellipse 170px 230px at 56% 78%,rgba(38,88,62,.95),rgba(38,88,62,0) 100%),
    radial-gradient(ellipse 190px 260px at 78% 72%,rgba(92,128,190,.95),rgba(92,128,190,0) 100%),
    radial-gradient(ellipse 150px 110px at 62% 28%,rgba(206,82,82,.35),rgba(206,82,82,0) 100%),
    radial-gradient(ellipse 360px 120px at 72% 14%,rgba(255,255,255,.85),rgba(255,255,255,0) 100%),
    linear-gradient(90deg,#f3f2f0 0%,#e7e5e1 42%,#cfccc6 72%,#b9b7b1 100%)}
.hero-title{left:75px;top:100px;color:var(--green);font-weight:800;line-height:1}
.hero-title .l1{font-size:46px}
.hero-title .l2{font-size:56px;margin-top:2px}
.hero-sub{left:75px;top:206px;font-size:32px;font-weight:700;color:var(--heading);line-height:40px}
.hero-note{left:75px;top:299px;font-size:13px;font-weight:700;color:var(--heading)}
.badge{left:75px;top:323px;width:215px;height:47px;background:var(--green);display:flex;align-items:center;gap:10px;padding-left:16px;color:var(--white);font-size:22px;font-weight:600}
.badge-square{width:20px;height:20px;background:var(--white)}
.dots{left:75px;top:420px;display:flex;gap:9px}
.dots span{width:12px;height:12px;border-radius:50%;background:#6b6b6b}
.dots span.on{background:var(--blue)}

/* sections */
.section-title{font-size:20px;font-weight:700;color:var(--blue);letter-spacing:.3px}
.center{text-align:center;width:1200px;left:0}
.btn{display:flex;align-items:center;justify-content:center;background:linear-gradient(180deg,#9bd24b,var(--green-dark));color:var(--white);font-size:13px;font-weight:700;letter-spacing:.4px;border-radius:2px}

.welcome{left:0;top:632px;width:1200px;height:317px}
.welcome p{position:absolute;left:60px;top:95px;width:1080px;text-align:center;font-size:14px;line-height:27px}

.treatments{left:0;top:949px;width:1200px;height:449px;background:var(--light-bg)}
.card{top:100px;width:242px}
.card-img{width:242px;height:167px}
.card h3{font-size:16px;font-weight:700;color:var(--green);margin-top:21px}
.card p{font-size:14px;line-height:23px;margin-top:8px;white-space:nowrap}

.team-advice{left:0;top:1398px;width:1200px;height:395px}
.team-advice h2{position:absolute;top:42px;font-size:22px;font-weight:700;color:var(--blue)}
.team-photo{left:75px;top:91px;width:211px;height:269px;
  background:
    radial-gradient(ellipse 60px 150px at 28% 72%,rgba(36,84,62,.95),rgba(36,84,62,0) 100%),
    radial-gradient(ellipse 60px 150px at 68% 70%,rgba(96,132,196,.95),rgba(96,132,196,0) 100%),
    radial-gradient(ellipse 90px 30px at 60% 8%,rgba(205,75,75,.45),rgba(205,75,75,0) 100%),
    linear-gradient(180deg,#eceae6,#d8d6d1 60%,#9ca29f)}
.team-text{left:304px;top:85px;width:390px;font-size:14px;line-height:27px;white-space:nowrap}
.video{left:704px;top:91px;width:422px;height:269px;overflow:hidden;
  background:
    radial-gradient(ellipse 120px 70px at 20% 15%,rgba(222,204,170,.75),rgba(222,204,170,0) 100%),
    radial-gradient(ellipse 110px 120px at 30% 75%,rgba(96,82,100,.9),rgba(96,82,100,0) 100%),
    radial-gradient(ellipse 90px 130px at 78% 55%,rgba(120,128,150,.85),rgba(120,128,150,0) 100%),
    linear-gradient(135deg,#7d8485,#3f3d40 55%,#27272b)}
.play{left:186px;top:109px}

.band{left:0;top:1793px;width:1200px;height:89px;background:var(--blue);color:var(--white);font-weight:700}
.band-text{left:158px;top:0;line-height:89px;font-size:14.5px;letter-spacing:.3px}
.band-badge{left:654px;top:19px;width:211px;height:55px;border:2px solid var(--white);border-radius:3px;display:flex;align-items:center;gap:10px;padding-left:16px;font-size:22px;font-weight:600}
.band-note{left:878px;top:0;line-height:89px;font-size:13px}

.footer{left:0;top:1882px;width:1200px;height:270px;background:var(--footer);color:#e4e4e4}
.footer h4{font-size:14px;color:var(--green);font-weight:600;margin-bottom:14px}
.f-col{top:46px;font-size:13px;line-height:20px}
.f-brand{display:flex;align-items:center;gap:10px;margin-bottom:16px}
.f-brand .brand-mark{background:#d9d9d9}
.f-brand .brand-name{color:var(--white);font-size:21px}
.f-brand .brand-sub{color:var(--white)}
.f-links li{list-style:none;line-height:31px}
.f-strong{font-weight:700;color:var(--white);font-size:12.5px}
.f-row{display:flex;align-items:center;gap:12px;line-height:25px}
.f-row svg{width:12px;height:12px;fill:#e4e4e4}
.social{display:flex;gap:6px}
.social span{width:29px;height:29px;border-radius:50%}
.footer-bottom{left:0;top:2152px;width:1200px;height:62px;background:var(--footer-bottom);color:#a9a9a9;font-size:12.5px;text-align:center;line-height:62px}
</style>
</head>
<body>

<div class="abs top-line"></div>

<header>
  <div class="abs brand">
    <span class="brand-mark"></span>
    <div>
      <div class="brand-name">The Harbourlight</div>
      <div class="brand-sub">DENTAL CENTRE</div>
    </div>
  </div>
  <div class="abs info-block" style="left:731px">
    <h4>CONTACT ADDRESS:</h4>
    <div class="info-row"><svg viewBox="0 0 24 24"><path d="M6.6 10.8a15 15 0 0 0 6.6 6.6l2.2-2.2c.3-.3.7-.4 1-.2 1.1.4 2.3.6 3.6.6.6 0 1 .4 1 1V20c0 .6-.4 1-1 1A17 17 0 0 1 3 4c0-.6.4-1 1-1h3.5c.6 0 1 .4 1 1 0 1.3.2 2.5.6 3.6.1.3 0 .7-.2 1z"/></svg>08 7342 1180</div>
    <div class="info-row"><svg viewBox="0 0 24 24"><path d="M2 5h20v14H2zM2 5l10 8 10-8" stroke="#fff" stroke-width="1.5"/></svg>info@harbourlightdental.com</div>
  </div>
  <div class="abs info-block" style="left:948px">
    <h4>OPENING HOURS:</h4>
    <div>Open 8 Am To 8pm 7 Days</div>
    <div>A Week</div>
  </div>
</header>

<nav class="abs nav">
  <a href="#" style="left:75px">HOME</a>
  <a href="#" style="left:180px">ABOUT TEAM</a>
  <a href="#" style="left:331px">DENTAL TREATMENTS</a>
  <a href="#" style="left:539px">DENTAL ADVICE</a>
  <a href="#" style="left:707px">CLINIC TIDAL</a>
  <a href="#" style="left:878px">CONTACT US</a>
</nav>

<section class="abs hero" role="img" aria-label="Photo of the husband and wife dentists in scrubs at the Guatemala dental mission">
  <div class="abs hero-title"><div class="l1">The Harbourlight</div><div class="l2">Dental Care</div></div>
  <div class="abs hero-sub">We offer a walk in service for<br>dental treatments</div>
  <div class="abs hero-note">No Need of Appointment</div>
  <div class="abs badge"><span class="badge-square"></span>Clinic Tidal</div>
  <div class="abs dots"><span class="on"></span><span></span><span></span><span></span></div>
</section>

<section class="abs welcome">
  <h2 class="abs center section-title" style="top:50px">WELCOME TO OUR WEBSITE</h2>
  <p>Aliquam molestie, mi et imperdiet euismod, dui purus auctor tellus, et interdum lacus lectus et ante. Sed accumsan sollicitudin sapien, sit amet<br>adipiscing turpis gravida ac. In congue, neque ac lobortis volutpat, libero mauris varius mi, vitae suscipit ipsum ligula vitae risus. Duis aliquam nibh<br>a dui iaculis viverra id a velit. Vivamus egestas risus in magna varius commodo. Sed semper viverra egestas. Etiam pretium porttitor lectus,<br>vel ornare neque porta volutpat.</p>
  <a href="#" class="abs btn" style="left:524px;top:237px;width:152px;height:44px">READ MORE</a>
</section>

<section class="abs treatments">
  <h2 class="abs center section-title" style="top:48px">TREATMENTS WE OFFER</h2>
  <article class="abs card" style="left:75px">
    <div class="card-img" role="img" aria-label="Close-up photo of a tooth with a filling" style="background:radial-gradient(ellipse 90px 70px at 45% 45%,#f1e6d6,rgba(241,230,214,0) 100%),radial-gradient(ellipse 40px 30px at 45% 40%,#7d5a44,rgba(125,90,68,0) 100%),linear-gradient(135deg,#c9564f,#d88c80 50%,#a8373a)"></div>
    <h3>Fillings</h3>
    <p>Technological advances have<br>rendered cosmetic white fillings<br>as strong and reliable as the<br>traditional mercury..</p>
  </article>
  <article class="abs card" style="left:344px">
    <div class="card-img" role="img" aria-label="Photo of a patient receiving root canal treatment" style="background:radial-gradient(ellipse 80px 60px at 60% 70%,#b48f7c,rgba(180,143,124,0) 100%),radial-gradient(ellipse 70px 50px at 25% 20%,#e6eef1,rgba(230,238,241,0) 100%),linear-gradient(135deg,#6d8c9c,#a9bcc4 50%,#51646e)"></div>
    <h3>Root Canal Treatment</h3>
    <p>Root canal therapy (RCT) is a<br>technique used to retain a tooth<br>with an irreversibly damaged<br>nerve...</p>
  </article>
  <article class="abs card" style="left:615px">
    <div class="card-img" role="img" aria-label="Photo of a smile before and after teeth whitening" style="background:radial-gradient(ellipse 110px 28px at 50% 48%,#fbf8f1,rgba(251,248,241,0) 100%),linear-gradient(180deg,#eab4a6,#e59a8c 40%,#e59a8c 60%,#d98578)"></div>
    <h3>Teeth Whitening</h3>
    <p>Now you can whiten your smile<br>with our custom fitted whitening<br>trays in the comfort of your<br>own home..</p>
  </article>
  <article class="abs card" style="left:884px">
    <div class="card-img" role="img" aria-label="Photo of a dental crown model" style="background:radial-gradient(ellipse 45px 38px at 45% 55%,#c99a4a,rgba(201,154,74,0) 100%),radial-gradient(ellipse 50px 45px at 70% 45%,#f7eef2,rgba(247,238,242,0) 100%),linear-gradient(135deg,#e46fa5,#f0b8d0 55%,#d95390)"></div>
    <h3>Crowns and Bridges</h3>
    <p>A crown (cap) is a covering that<br>encases the entire tooth surface,<br>thus restoring it to its original<br>shape, size, and colour..</p>
  </article>
</section>

<section class="abs team-advice">
  <h2 style="left:75px">MEET THE TEAM</h2>
  <div class="abs team-photo" role="img" aria-label="Photo of the dentist couple standing together"></div>
  <p class="abs team-text">Aliquam molestie, mi et imperdiet euismod, dui<br>purus auctor tellus, et interdum lacus lectus et ante.<br>Sed accumsan sollicitudin sapien, sit amet<br>adipiscing turpis gravida ac. In congue, neque ac<br>lobortis volutpat, libero mauris varius mi, vitae<br>suscipit ipsum ligula vitae risus. Duis aliquam nibh a<br>dui iaculis viverra id a velit. Vivamus egestas risus in<br>magna varius commodo.</p>
  <a href="#" class="abs btn" style="left:303px;top:316px;width:152px;height:44px">READ MORE</a>

  <h2 style="left:704px">DENTAL ADVICE</h2>
  <div class="abs video" role="img" aria-label="Video still of patients waiting at the dental mission clinic">
    <svg class="abs play" width="52" height="52" viewBox="0 0 52 52"><circle cx="26" cy="26" r="23" fill="none" stroke="#fff" stroke-width="4"/><path d="M20 15 L37 26 L20 37Z" fill="#fff"/></svg>
  </div>
</section>

<section class="abs band">
  <div class="abs band-text">AENEAN A NIBH EGET TURPIS VEHICULA TEMPUS AC SED MASSA.</div>
  <div class="abs band-badge"><span class="badge-square"></span>Clinic Tidal</div>
  <div class="abs band-note">No Need of Appointment</div>
</section>

<footer class="abs footer">
  <div class="abs f-col" style="left:77px;width:320px">
    <div class="f-brand">
      <span class="brand-mark"></span>
      <div><div class="brand-name">The Harbourlight</div><div class="brand-sub">DENTAL CENTRE</div></div>
    </div>
    <p style="line-height:23px;white-space:nowrap">Duis aliquam nibh a dui iaculis viverra id a<br>velit. Vivamus egestas risus in magna varius<br>commodo. Sed semper viverra egestas.</p>
    <a href="#" style="color:var(--green);display:block;margin-top:12px">Learn More</a>
  </div>
  <div class="abs f-col" style="left:434px">
    <h4>QUICK LINKS</h4>
    <ul class="f-links" style="margin-top:-6px">
      <li>Home</li><li>About Team</li><li>Dental Treatments</li><li>Dental Advice</li><li>Clinic Tidal</li><li>Contact Us</li>
    </ul>
  </div>
  <div class="abs f-col" style="left:624px;width:240px">
    <h4>CONTACT US</h4>
    <div class="f-strong">HARBOURLIGHT DENTAL CENTRE</div>
    <div style="margin-top:2px;line-height:22px">Unit 7, 18 Bayview Parade,<br>Northcliff, WA 6071.</div>
    <div class="f-row" style="margin-top:12px"><svg viewBox="0 0 24 24"><path d="M6.6 10.8a15 15 0 0 0 6.6 6.6l2.2-2.2c.3-.3.7-.4 1-.2 1.1.4 2.3.6 3.6.6.6 0 1 .4 1 1V20c0 .6-.4 1-1 1A17 17 0 0 1 3 4c0-.6.4-1 1-1h3.5c.6 0 1 .4 1 1 0 1.3.2 2.5.6 3.6.1.3 0 .7-.2 1z"/></svg>08 7342 1180</div>
    <div class="f-row"><svg viewBox="0 0 24 24"><path d="M2 5h20v14H2z"/></svg>info@harbourlightdental.com</div>
    <div class="f-row"><svg viewBox="0 0 24 24"><path d="M12 2a7 7 0 0 0-7 7c0 5 7 13 7 13s7-8 7-13a7 7 0 0 0-7-7zm0 9.5a2.5 2.5 0 1 1 0-5 2.5 2.5 0 0 1 0 5z"/></svg>Get Map Direction</div>
  </div>
  <div class="abs f-col" style="left:886px">
    <h4>OPENING TIMES</h4>
    <div class="f-strong">OPEN 8 AM TO 8PM 7 DAYS A WEEK</div>
    <h4 style="margin-top:44px">CONNECT US</h4>
    <div class="social">
      <span style="background:#3b5b98"></span>
      <span style="background:#2aa3e0"></span>
      <span style="background:#3a3a3a"></span>
      <span style="background:#cc2127"></span>
      <span style="background:#dd4b39"></span>
      <span style="background:#d9302b"></span>
    </div>
  </div>
</footer>

<div class="abs footer-bottom">Copyright © 2016. The Harbourlight Dental Centre All Right Reserved</div>

</body>
</html>
```